Falkrin homes and renovations business card design.

Would like some new card designs utilizing my new logo that look professional. I am open to different colors on the logo or utilize the same ones we have. I like the original concept but would like to see some fresh ideas and build on what we have already done.

Target Market(s)

Custom home building industry, Real estate sales, Renovation projects.

Industry/Entity Type

Home Builder

Contact Information for Business Card

Falkrin Homes and Renovations
2871 96th Avenue
Halden Ridge, Northvale
T2R3W8
Home : 403- 718-4063 Cell: 403- 294-5170

My info is : Dax Falkrin, President and CEO
email: falkrinhomes@maildrop-example.net
Website: falkrinhomes-example.com
websit

Requirements
Must have
• Must Use my new logo design. I am open to different colors on the logo or utilize the same ones in the existing design. I can upload the original logo design if needed.

```html
<!DOCTYPE html>
<html lang="en">
<head>
<meta charset="utf-8">
<title>Falkrin Homes and Renovations – Business Card</title>
<link rel="stylesheet" href="https://fonts.googleapis.com/css2?family=Open+Sans:wght@400;600;700&display=swap">
<style>
  :root {
    --gold: #b5883a;
    --card-white: #f6f6f5;
    --ink: #2e2e2e;
    --icon-grey: #9a9a9a;
    --backdrop: #e9e7e4;
    --on-gold: #ffffff;
  }
  html, body {
    margin: 0;
    width: 1200px;
    height: 900px;
    overflow: hidden;
    background: var(--backdrop);
    font-family: "Open Sans", Arial, sans-serif;
  }
  .stage {
    position: relative;
    width: 1200px;
    height: 900px;
  }
  .business-card {
    position: absolute;
    left: 150px;
    top: 172px;
    width: 900px;
    height: 555px;
    filter: drop-shadow(0 10px 24px rgba(0,0,0,0.18));
  }
  .card-text { font-family: "Open Sans", Arial, sans-serif; }
  .holder-name { font-size: 27px; font-weight: 700; fill: var(--on-gold); letter-spacing: 0.3px; }
  .holder-title { font-size: 16px; font-weight: 400; fill: var(--on-gold); }
  .contact-line { font-size: 14.5px; font-weight: 400; fill: var(--ink); }
  .company-name { font-size: 27px; font-weight: 600; fill: var(--gold); }
  .address-line { font-size: 15.5px; font-weight: 400; fill: var(--on-gold); }
  .icon { fill: var(--icon-grey); }
  .icon-stroke { fill: none; stroke: var(--icon-grey); stroke-width: 1.4; }
</style>
</head>
<body>
<main class="stage">
  <svg class="business-card" viewBox="0 0 652 402" role="group" aria-label="Falkrin Homes and Renovations business card">
    <defs>
      <clipPath id="card-shape">
        <rect x="0" y="0" width="652" height="402" rx="14" ry="14"/>
      </clipPath>
    </defs>
    <g clip-path="url(#card-shape)">
      <rect class="card-base" x="0" y="0" width="652" height="402" fill="var(--gold)"/>
      <polygon class="roof-panel" points="0,110 190,45 385,140 652,140 652,320 0,320" fill="var(--card-white)"/>
    </g>

    <g class="card-text">
      <text class="holder-name" x="622" y="72" text-anchor="end">DAX FALKRIN</text>
      <text class="holder-title" x="622" y="99" text-anchor="end">President and CEO</text>

      <text class="company-name" x="28" y="222">Falkrin Homes</text>
      <text class="company-name" x="28" y="256">and Renovations</text>

      <text class="contact-line" x="600" y="207" text-anchor="end">403- 718-4063</text>
      <text class="contact-line" x="600" y="231" text-anchor="end">403- 294-5170</text>
      <text class="contact-line" x="600" y="255" text-anchor="end">falkrinhomes@maildrop-example.net</text>
      <text class="contact-line" x="600" y="279" text-anchor="end">www.falkrinhomes-example.com</text>

      <text class="address-line" x="622" y="370" text-anchor="end">2871 96th Avenue Halden Ridge, Northvale T2R3W8</text>
    </g>

    <g class="contact-icons">
      <path class="icon phone-icon" d="M609 197 q6 -4 12 0 l0 3 l-3 0 l0 -1 q-3 -1 -6 0 l0 1 l-3 0 z M610 203 h10 l-1 4 h-8 z"/>
      <rect class="icon-stroke mobile-icon" x="612" y="219" width="7" height="12" rx="1.5"/>
      <g class="email-icon">
        <rect class="icon" x="609" y="246" width="13" height="9"/>
        <polyline points="609,246 615.5,251.5 622,246" fill="none" stroke="var(--card-white)" stroke-width="1.2"/>
      </g>
      <g class="web-icon">
        <circle class="icon" cx="615.5" cy="274" r="6"/>
        <ellipse cx="615.5" cy="274" rx="2.5" ry="6" fill="none" stroke="var(--card-white)" stroke-width="0.9"/>
        <line x1="609.5" y1="274" x2="621.5" y2="274" stroke="var(--card-white)" stroke-width="0.9"/>
      </g>
    </g>
  </svg>
</main>
</body>
</html>
```